We (R. T. Galvin & Partners, Inc.) are an executive Search firm based in Los Angeles that is exclusively focused in the Med Tech and Health Tech arenas.   I need a logo to communicate that we are a high end search firm, but also that we are focused in the medicine and science arenas called health tech and med tech.  Many of our clients have robotics and artificial intelligence type products, so it is very technology forward.  I tend to gravitate towards clean, sharp aesthetic as opposed to something that is really over the top.
Attached are files with my logo in two different layouts.  In addition to the letterhead and envelope, I also will need an electronic letterhead in Microsoft Word.  I tend to
I look forward to seeing the designs and just let me know if you have any questions.
Dale

```html
<!DOCTYPE html>
<html lang="en">
<head>
<meta charset="utf-8">
<title>R. T. Galvin &amp; Partners, Inc. — Business Card</title>
<link rel="stylesheet" href="https://fonts.googleapis.com/css2?family=Montserrat:wght@500;600&family=Roboto:wght@400&display=swap">
<style>
  :root {
    --bg: #b0b0ac;
    --card: #ffffff;
    --brand-blue: #4fa0dc;
    --edge-blue: #3f95d8;
    --ink: #111111;
    --text-grey: #555555;
    --tint: #e3f0f9;
  }
  * { box-sizing: border-box; margin: 0; padding: 0; }
  html, body {
    width: 1200px; height: 801px; overflow: hidden;
    background: var(--bg);
  }
  .stage {
    width: 1200px; height: 801px;
    display: flex; align-items: center; justify-content: center; gap: 48px;
  }
  .card {
    position: relative;
    width: 530px; height: 310px;
    background: var(--card);
    border-radius: 28px;
    border-bottom: 4px solid var(--edge-blue);
    overflow: hidden;
  }

  /* front face */
  .card-front { display: flex; align-items: center; }
  .brand-block {
    width: 240px; padding-left: 34px;
    display: flex; align-items: center; gap: 12px;
  }
  .brand-mark {
    width: 22px; height: 22px; border-radius: 50%;
    background: var(--brand-blue); flex: none;
  }
  .brand-name {
    font-family: "Montserrat", sans-serif; font-weight: 500;
    color: var(--ink); line-height: 1.15;
    font-size: 19px; letter-spacing: 0.5px;
  }
  .brand-name .line-two {
    display: block; font-size: 10.5px; letter-spacing: 2.6px;
  }
  .divider {
    width: 1.5px; height: 150px; background: var(--brand-blue);
  }
  .contact-block { padding-left: 26px; }
  .person-name {
    font-family: "Montserrat", sans-serif; font-weight: 600;
    color: var(--brand-blue); font-size: 25px; letter-spacing: 1px;
    text-transform: uppercase;
  }
  .person-role, .contact-line {
    font-family: "Roboto", sans-serif; color: var(--text-grey);
    font-size: 12.5px; line-height: 1.45;
  }
  .person-role { margin-bottom: 8px; }
  .address { margin-bottom: 8px; }
  .contact-line { display: flex; align-items: center; gap: 7px; }
  .contact-line svg { width: 11px; height: 11px; flex: none; }

  /* back face */
  .card-back { display: flex; align-items: center; justify-content: center; }
  .back-pattern {
    position: absolute; inset: 0;
    background: radial-gradient(circle at 50% 45%, var(--tint) 0%, #f4f9fd 45%, var(--card) 80%);
  }
  .back-brand {
    position: relative; display: flex; align-items: center; gap: 16px;
  }
  .back-brand .brand-mark { width: 30px; height: 30px; }
  .back-brand .brand-name { font-size: 38px; letter-spacing: 1px; }
  .back-brand .brand-name .line-two { font-size: 17px; letter-spacing: 6px; }
</style>
</head>
<body>
<main class="stage">
  <section class="card card-front">
    <div class="brand-block">
      <span class="brand-mark"></span>
      <p class="brand-name">R. T. GALVIN<span class="line-two">&amp; PARTNERS INC.</span></p>
    </div>
    <div class="divider"></div>
    <div class="contact-block">
      <h1 class="person-name">Colin Harper</h1>
      <p class="person-role">Director</p>
      <p class="contact-line address">418 Ridgeway Court<br>Pine Falls, WI 53020</p>
      <p class="contact-line">
        <svg viewBox="0 0 12 12"><path d="M3 1 L5 3.5 L4 4.8 Q5 7 7.2 8 L8.5 7 L11 9 L9.8 11 Q4 10.5 1 3 Z" fill="var(--brand-blue)"/></svg>
        +49(4)421-70 31285
      </p>
      <p class="contact-line">
        <svg viewBox="0 0 12 12"><rect x="3" y="0.5" width="6" height="11" rx="1.2" fill="var(--brand-blue)"/><rect x="4" y="2" width="4" height="7" fill="#fff"/></svg>
        +49(0)162-4418702
      </p>
      <p class="contact-line">
        <svg viewBox="0 0 12 12"><rect x="0.8" y="2.3" width="10.4" height="7.4" fill="none" stroke="var(--brand-blue)" stroke-width="1.2"/><path d="M1 2.6 L6 6.6 L11 2.6" fill="none" stroke="var(--brand-blue)" stroke-width="1.2"/></svg>
        R. T. Galvin@Partners, Inc.com
      </p>
      <p class="contact-line">
        <svg viewBox="0 0 12 12"><circle cx="6" cy="6" r="5" fill="none" stroke="var(--brand-blue)" stroke-width="1.1"/><ellipse cx="6" cy="6" rx="2.2" ry="5" fill="none" stroke="var(--brand-blue)" stroke-width="1"/><path d="M1 6 H11" stroke="var(--brand-blue)" stroke-width="1"/></svg>
        R. T. Galvin &amp; Partners, Inc.com
      </p>
    </div>
  </section>

  <section class="card card-back">
    <div class="back-pattern" role="img" aria-label="Soft scattered light-blue circles decorating the card background"></div>
    <div class="back-brand">
      <span class="brand-mark"></span>
      <p class="brand-name">R. T. GALVIN<span class="line-two">&amp; PARTNERS INC.</span></p>
    </div>
  </section>
</main>
</body>
</html>
```